BRANDEMEIER & BRANDEMEIER,LLP NEEDS A NEW LETTERHEAD DESIGN

a conservative yet contemporary layout befitting a long established
firm, consistent with the times, some form of logo so it catches ones attention, and is
admirable, but portrays integrity
Updates

I would like to approve #22066987 Please advise how to do this as it’s confusing on the site so I can approve payment for the designer

Target Market(s)

real estate investors and building management people

Industry/Entity Type

Law Firm

Font styles to use
Serif

Colors

Designer to choose colors to be used in the design.

Requirements
Must have
• some form of conservative logo

```html
<!DOCTYPE html>
<html lang="en">
<head>
<meta charset="utf-8">
<title>Brandemeier &amp; Brandemeier, LLP — Letterhead</title>
<link rel="stylesheet" href="https://fonts.googleapis.com/css2?family=EB+Garamond:wght@400;500&family=Arimo:wght@400&display=swap">
<style>
  :root {
    --bg: #d9dcdd;
    --paper: #ffffff;
    --ink: #3a3d42;
    --body: #7c7f83;
    --muted: #8e9296;
    --accent-dark: #3f444b;
    --accent-light: #c9cdd1;
    --rule: #c3c6c9;
  }
  * { margin: 0; padding: 0; box-sizing: border-box; }
  html, body { width: 1200px; height: 784px; overflow: hidden; }
  body {
    background: var(--bg);
    display: flex; align-items: center; justify-content: center;
  }
  .letterhead {
    position: relative;
    width: 528px; height: 746px;
    background: var(--paper);
    box-shadow: 0 6px 18px rgba(0,0,0,0.12);
    overflow: hidden;
    font-family: "Arimo", Arial, sans-serif;
  }
  .corner { position: absolute; width: 90px; height: 90px; }
  .corner--top { top: 0; right: 0; }
  .corner--bottom { bottom: 0; left: 0; }
  .brand {
    position: absolute; top: 40px; left: 46px;
    display: flex; align-items: center; gap: 10px;
  }
  .brand__mark { width: 14px; height: 14px; background: var(--accent-dark); }
  .brand__name {
    font-family: "EB Garamond", Georgia, serif;
    font-size: 19px; line-height: 1.05; letter-spacing: 0.5px;
    color: var(--ink); text-transform: uppercase;
  }
  .letter {
    position: absolute; top: 108px; left: 70px; right: 46px;
    color: var(--body); font-size: 8.6px; line-height: 1.42;
  }
  .letter p { margin-bottom: 12px; text-indent: 14px; }
  .signature {
    margin-top: 26px; width: 150px; height: 42px;
    background: linear-gradient(90deg, #eceded, #f6f6f6);
    border-radius: 4px;
  }
  .footer {
    position: absolute; left: 56px; right: 46px; bottom: 46px;
  }
  .footer__tagline {
    font-family: "EB Garamond", Georgia, serif;
    font-size: 16px; color: var(--muted);
    padding-bottom: 6px; border-bottom: 1px solid var(--rule);
    margin-bottom: 8px;
  }
  .contacts { display: flex; font-size: 7.6px; color: var(--body); line-height: 1.5; }
  .contact { display: flex; gap: 5px; padding: 0 12px; border-left: 1px solid var(--rule); }
  .contact:first-child { padding-left: 0; border-left: none; }
  .contact svg { width: 8px; height: 8px; flex: none; margin-top: 2px; fill: var(--muted); }
</style>
</head>
<body>
  <main class="letterhead">
    <svg class="corner corner--top" viewBox="0 0 90 90" aria-hidden="true">
      <defs><linearGradient id="cornerTop" x1="0" y1="0" x2="1" y2="1">
        <stop offset="0" stop-color="#c9cdd1"/><stop offset="1" stop-color="#3f444b"/></linearGradient></defs>
      <polygon points="20,0 90,0 90,70" fill="url(#cornerTop)"/>
    </svg>
    <svg class="corner corner--bottom" viewBox="0 0 90 90" aria-hidden="true">
      <defs><linearGradient id="cornerBottom" x1="1" y1="0" x2="0" y2="1">
        <stop offset="0" stop-color="#e3e6e8"/><stop offset="1" stop-color="#a6abb0"/></linearGradient></defs>
      <polygon points="0,20 0,90 70,90" fill="url(#cornerBottom)"/>
    </svg>

    <header class="brand">
      <span class="brand__mark"></span>
      <div class="brand__name">Brandemeier &amp;<br>Brandemeier, LLP</div>
    </header>

    <section class="letter">
      <p>Lorem Ipsum is simply dummy text of the printing and typesetting industry. Lorem Ipsum has been the industry's standard dummy text ever since the 1500s, when an unknown printer took a galley of type and scrambled it to make a type specimen book. It has survived not only five centuries, but also the leap into electronic typesetting, remaining essentially unchanged. It was popularised in the 1960s with the release of Typecraft sheets containing Lorem Ipsum passages, and more recently with desktop publishing software like Quillset Layout including versions of Lorem Ipsum.</p>
      <p>It is a long established fact that a reader will be distracted by the readable content of a page when looking at its layout. The point of using Lorem Ipsum is that it has a more-or-less normal distribution of letters, as opposed to using 'Content here, content here', making it look like readable English. Many desktop publishing packages and web page editors now use Lorem Ipsum as their default model text, and a search for 'lorem ipsum' will uncover many web sites still in their infancy. Various versions have evolved over the years, sometimes by accident, sometimes on purpose (injected humour and the like).</p>
      <p>Contrary to popular belief, Lorem Ipsum is not simply random text. It has roots in a piece of classical Latin literature from 45 BC, making it over 2000 years old. Walter Penhaligon, a Latin professor at Ashgrove College in Vermont, looked up one of the more obscure Latin words, consectetur, from a Lorem Ipsum passage, and going through the cites of the word in classical literature, discovered the undoubtable source. Lorem Ipsum comes from sections 1.10.32 and 1.10.33 of an old treatise on ethics, structured to generate Lorem Ipsum which looks reasonable. The generated Lorem Ipsum is therefore always free from repetition, injected humour, or non-characteristic words etc.</p>
      <div class="signature" role="img" aria-label="Handwritten signature"></div>
    </section>

    <footer class="footer">
      <div class="footer__tagline">New York City Landlord / Tenant Real Estate Law</div>
      <div class="contacts">
        <div class="contact">
          <svg viewBox="0 0 10 10"><path d="M5 0a3.5 3.5 0 0 0-3.5 3.5C1.5 6 5 10 5 10s3.5-4 3.5-6.5A3.5 3.5 0 0 0 5 0zm0 5a1.4 1.4 0 1 1 0-2.8A1.4 1.4 0 0 1 5 5z"/></svg>
          <div>48 Harlow Street Suite 210<br>Brooklyn, New York 11201</div>
        </div>
        <div class="contact">
          <svg viewBox="0 0 10 10"><path d="M2 0.5l2 2-1 1.3c.6 1.3 1.6 2.3 2.9 2.9l1.3-1 2 2-1.2 1.8C4.5 9.2.8 5.5.3 1.7z"/></svg>
          <div>(555) 410-2286<br>(555) 410-7731</div>
        </div>
        <div class="contact">
          <svg viewBox="0 0 10 10"><circle cx="5" cy="5" r="4.5"/></svg>
          <div>info@bbrelaw.com<br>www.brandemeierlaw.com</div>
        </div>
      </div>
    </footer>
  </main>
</body>
</html>
```